Business Card Design for Marketing Firm

Looking for business card design for higher end marketing firm. Clean but impressionable/trendy. We are a marketing firm that represents manufacturers in the foodservice equipment and supply industry. Our customers are end users such has hotels, restaurants, country clubs, convention centers and casinos as well as distributors of restaurants supplies and equipment, and manufacturers of foodservice equipment and supplies.
Target Market(s)
Hotels, Restaurants, Supply & Equipment Distributors, Foodservice Manufacturers
Industry/Entity Type
Foodservice/Hospitality
Contact Information for Business Card
Name, Title, Contact Number, Email, Website, Social Media, Address
Requirements
Must have
- Clean & Simple but Serious and Impressionable

```html
<!DOCTYPE html>
<html lang="en">
<head>
<meta charset="utf-8">
<title>Harbor Service Reps – Business Card</title>
<link rel="stylesheet" href="https://fonts.googleapis.com/css2?family=Cinzel:wght@700&family=Arimo:wght@400&display=swap">
<style>
  :root {
    --navy: #1b1f5c;
    --ink: #4a4a4f;
    --paper: #fbfbfb;
    --backdrop: #cfd2d3;
    --rule: #3b3f86;
  }
  * { margin: 0; padding: 0; box-sizing: border-box; }
  html, body { width: 1200px; height: 829px; overflow: hidden; }
  body {
    background: var(--backdrop);
    font-family: "Arimo", Arial, sans-serif;
    position: relative;
  }
  .card {
    position: absolute;
    width: 520px;
    height: 297px;
    background: var(--paper);
    box-shadow: 0 10px 24px rgba(0,0,0,0.12);
    overflow: hidden;
  }
  .card--front { left: 50px; top: 266px; }
  .card--back { left: 630px; top: 266px; border-bottom: 5px solid var(--navy); }

  .holder { position: absolute; left: 30px; top: 32px; }
  .holder__name {
    font-family: "Cinzel", Georgia, serif;
    font-weight: 700;
    font-size: 19px;
    color: var(--navy);
    letter-spacing: 0.5px;
  }
  .holder__title { font-size: 11.5px; color: var(--ink); margin-top: 3px; }
  .holder__rule { width: 190px; height: 1px; background: var(--rule); margin-top: 10px; }

  .contact { position: absolute; left: 30px; top: 100px; list-style: none; }
  .contact__item {
    display: flex; align-items: center; gap: 7px;
    font-size: 11.5px; color: var(--ink); line-height: 20px;
  }
  .contact__icon { width: 10px; height: 10px; fill: var(--navy); flex: none; }

  .brand {
    position: absolute;
    display: flex; align-items: center; gap: 8px;
    font-family: "Cinzel", Georgia, serif; font-weight: 700; color: var(--navy);
    white-space: nowrap;
  }
  .brand__dot { border-radius: 50%; background: var(--navy); flex: none; }

  .card--front .brand { right: 30px; top: 130px; font-size: 17px; }
  .card--front .brand__dot { width: 10px; height: 10px; }

  .long-rule {
    position: absolute; left: 30px; right: 30px; top: 190px;
    height: 1px; background: var(--rule);
  }

  .address {
    position: absolute; right: 30px; top: 204px;
    font-size: 11.5px; font-style: normal; color: var(--ink); line-height: 16px; text-align: left;
  }

  .band { position: absolute; left: 0; bottom: 0; width: 520px; height: 40px; }
  .band__fill { fill: var(--navy); }
  .band__handle {
    position: absolute; right: 30px; bottom: 9px;
    display: flex; align-items: center; gap: 6px;
    color: #fff; font-size: 12px;
  }
  .band__dot { width: 9px; height: 9px; border-radius: 50%; background: #fff; }

  .card--back .brand { left: 50%; top: 50%; transform: translate(-50%, -50%); font-size: 26px; }
  .card--back .brand__dot { width: 14px; height: 14px; }
</style>
</head>
<body>
  <article class="card card--front">
    <div class="holder">
      <h1 class="holder__name">Daniel Whitford</h1>
      <p class="holder__title">CEO/Founder</p>
      <div class="holder__rule"></div>
    </div>

    <ul class="contact">
      <li class="contact__item">
        <svg class="contact__icon" viewBox="0 0 10 10"><path d="M2 0.5l2 2-1 1.2c.6 1.3 1.6 2.3 2.8 2.8l1.2-1 2 2-1.3 1.7C4.2 9.3.7 5.8.3 1.8z"/></svg>
        555-014-2290
      </li>
      <li class="contact__item">
        <svg class="contact__icon" viewBox="0 0 10 10"><path d="M0 2h10v6H0z M0.6 2.4L5 5.6l4.4-3.2" stroke="#fff" stroke-width="0.8"/></svg>
        info@harborservicereps.com
      </li>
      <li class="contact__item">
        <svg class="contact__icon" viewBox="0 0 10 10"><circle cx="5" cy="5" r="4.6"/><path d="M0.5 5h9M5 0.5c-2.4 2.6-2.4 6.4 0 9M5 0.5c2.4 2.6 2.4 6.4 0 9" stroke="#fff" stroke-width="0.7" fill="none"/></svg>
        www.harborservicereps.com
      </li>
    </ul>

    <div class="brand"><span class="brand__dot"></span>Harbor Service Reps</div>

    <div class="long-rule"></div>

    <address class="address">
      48 Maple Avenue, Suite 210<br>
      Lakeview, ST 40210
    </address>

    <svg class="band" viewBox="0 0 520 40" preserveAspectRatio="none" aria-hidden="true">
      <path class="band__fill" d="M0 33 H240 C258 33 262 8 285 8 H520 V40 H0 Z"/>
      <path class="band__fill" d="M0 24 H232 V27 H0 Z"/>
    </svg>
    <div class="band__handle">@harborservicereps <span class="band__dot"></span><span class="band__dot"></span></div>
  </article>

  <article class="card card--back">
    <div class="brand"><span class="brand__dot"></span>Harbor Service Reps</div>
  </article>
</body>
</html>
```